Brindlecourt Air Business Card Design

Design new, 2 sides, business cards for a residential and light commercial heating, air conditioning contractor.

Target Market(s)

Homeowners, small businesses

Industry/Entity Type

Business

Contact Information for Business Card

Dominic Westerhall
Phone - 862-415-2736
Email
Address - PO box 518
Brightwater NJ 07912
Website - www.HarborBreezeLLC.example

Requirements
Must have
• logo, company colors, standard size with no die cut, so I can use nova stamp

```html
<!DOCTYPE html>
<html lang="en">
<head>
<meta charset="utf-8">
<title>Brindlecourt Air Business Cards</title>
<link href="https://fonts.googleapis.com/css2?family=Open+Sans:ital,wght@0,400;0,600;0,700;1,400&display=swap" rel="stylesheet">
<style>
  :root {
    --crimson: #9b2335;
    --orange: #f5882f;
    --accent-orange: #f7a21b;
    --white: #ffffff;
    --ink: #3a1717;
    --backdrop: #dcdcdc;
  }
  * { margin: 0; padding: 0; box-sizing: border-box; }
  html, body {
    width: 1105px; height: 1200px; overflow: hidden;
    background: var(--backdrop);
    font-family: "Open Sans", Arial, sans-serif;
  }
  .canvas { position: relative; width: 1105px; height: 1200px; }
  .card {
    position: absolute; left: 196px;
    width: 720px; height: 414px;
    border-radius: 19px; overflow: hidden;
  }
  .card--front { top: 145px; background: var(--white); }
  .card--back { top: 602px; background: var(--orange); }
  .card__shapes { position: absolute; left: 0; top: 0; width: 720px; height: 414px; }

  .contact { position: absolute; left: 36px; top: 0; color: var(--white); }
  .contact__name { position: absolute; top: 50px; white-space: nowrap; font-size: 23px; line-height: 32px; font-weight: 700; text-transform: uppercase; }
  .contact__title { position: absolute; top: 84px; white-space: nowrap; font-size: 18px; line-height: 26px; }
  .contact__address { position: absolute; top: 179px; white-space: nowrap; font-size: 18px; line-height: 28px; }
  .contact__list { position: absolute; top: 239px; list-style: none; font-size: 18px; line-height: 27.5px; white-space: nowrap; }
  .contact__list li { display: flex; align-items: center; gap: 10px; }
  .contact__list svg { width: 16px; height: 16px; fill: var(--white); flex: none; }

  .brand-name {
    position: absolute; color: var(--crimson);
    font-weight: 700; white-space: nowrap; line-height: 1;
    transform: translate(-50%, -50%);
  }
  .card--front .brand-name { left: 529px; top: 200px; font-size: 31px; }
  .card--back .brand-name { left: 360px; top: 178px; font-size: 46px; }

  .tagline {
    position: absolute; left: 0; width: 720px; top: 313px;
    text-align: center; font-style: italic; font-size: 17px; line-height: 25px;
    color: var(--ink);
  }
</style>
</head>
<body>
<div class="canvas">

  <section class="card card--front" aria-label="Business card front">
    <svg class="card__shapes" viewBox="0 0 522 300" preserveAspectRatio="none" aria-hidden="true">
      <path d="M280 0 H300 C238 60 222 180 318 300 H300 C210 180 220 70 280 0 Z" fill="var(--accent-orange)"/>
      <path d="M0 0 H288 C225 65 210 185 318 300 H0 Z" fill="var(--crimson)"/>
    </svg>

    <div class="contact">
      <p class="contact__name">Dominic Westerhall</p>
      <p class="contact__title">CEO/Founder</p>
      <p class="contact__address">PO box 518<br>Brightwater NJ 07912</p>
      <ul class="contact__list">
        <li>
          <svg viewBox="0 0 24 24"><path d="M6.6 10.8a15.1 15.1 0 0 0 6.6 6.6l2.2-2.2a1 1 0 0 1 1-.25 11.4 11.4 0 0 0 3.6.57 1 1 0 0 1 1 1V20a1 1 0 0 1-1 1A17 17 0 0 1 3 4a1 1 0 0 1 1-1h3.5a1 1 0 0 1 1 1c0 1.25.2 2.45.57 3.57a1 1 0 0 1-.25 1z"/></svg>
          <span>862 415 2736</span>
        </li>
        <li>
          <svg viewBox="0 0 24 24"><path d="M7 1h10a2 2 0 0 1 2 2v18a2 2 0 0 1-2 2H7a2 2 0 0 1-2-2V3a2 2 0 0 1 2-2zm0 3v14h10V4zm5 15.5a1.2 1.2 0 1 0 0 2.4 1.2 1.2 0 0 0 0-2.4z"/></svg>
          <span>862 415 2790</span>
        </li>
        <li>
          <svg viewBox="0 0 24 24"><path d="M6 2h12v6H6zM3 9h18a2 2 0 0 1 2 2v7h-4v4H5v-4H1v-7a2 2 0 0 1 2-2zm4 7v4h10v-4z"/></svg>
          <span>862 415 2744</span>
        </li>
        <li>
          <svg viewBox="0 0 24 24"><path d="M2 5h20v14H2zm2 2v.5l8 5 8-5V7l-8 5z"/></svg>
          <span>dominic@brindlecourt.example</span>
        </li>
        <li>
          <svg viewBox="0 0 24 24"><path d="M12 2a10 10 0 1 0 0 20 10 10 0 0 0 0-20zm6.9 6h-3a15.6 15.6 0 0 0-1.4-3.6A8 8 0 0 1 18.9 8zM12 4a14 14 0 0 1 1.9 4h-3.8A14 14 0 0 1 12 4zM4.3 14a8 8 0 0 1 0-4h3.4a16 16 0 0 0 0 4zm.8 2h3a15.6 15.6 0 0 0 1.4 3.6A8 8 0 0 1 5.1 16zm3-8h-3a8 8 0 0 1 4.4-3.6A15.6 15.6 0 0 0 8.1 8zM12 20a14 14 0 0 1-1.9-4h3.8A14 14 0 0 1 12 20zm2.3-6H9.7a14.7 14.7 0 0 1 0-4h4.6a14.7 14.7 0 0 1 0 4zm.2 5.6a15.6 15.6 0 0 0 1.4-3.6h3a8 8 0 0 1-4.4 3.6zm1.8-5.6a16 16 0 0 0 0-4h3.4a8 8 0 0 1 0 4z"/></svg>
          <span>www.BrindlecourtLLC.example</span>
        </li>
      </ul>
    </div>

    <p class="brand-name">Brindlecourt Air</p>
  </section>

  <section class="card card--back" aria-label="Business card back">
    <p class="brand-name">Brindlecourt Air</p>
    <p class="tagline">Residential &amp; light commercial heating<br>Air conditioning contractor</p>
  </section>

</div>
</body>
</html>
```